develop our online residential property development appraisal service

This project requires a detailed WordPress design to represent a new digital residential property development consultancy business. At its heart it will have a number of different products that essentially advise customers of the potential value and feasibility of developing their residential site into multiple townhouses, units, apartments, etc... This will be accompanied by explaining the considerations of residential property development.

We aim to navigate and break down this complex area and provide our customers with the tools, knowledge, control and power to 'unlock the value' in their property.

REFERENCE DOCUMENTS:
1. Detailed solution requirements please refer to the attached 'wordpressdesignrequirements'
2. Logo files, style guide and colour pallet please refer to the attached 'KRLM.zip'
3. Site Map refer to attached 'wordpressdesignsitemap'

Reason: Additional information provided so extending period for designs to take into account.

Target Market(s)

The site will appeal to professional service providers; accountants, financial planners, lawyers, etc…

Industry/Entity Type

Residential

Font styles to use
Sans Serif
Other font styles liked:
• Similar to the logo font, slim line and simple

Requirements
Must have
• The logo, style and colour palette provided in the attached 'KRLM.zip' files
• Satisfy the intent of the 'wordpressdesignrequirements'
• Present as an online-centric business
• Clean, crisp and modern design
• Predominant use of white as a background contrasted with the colours provided in the colour palette
Nice to have
• Use of the following WordPress business themes is encouraged but not mandatory:
• 1. Mavo
• 2. Tulek
• 3. Vupa
Should not have
• Overt references to Australia

```html
<!DOCTYPE html>
<html lang="en">
<head>
<meta charset="utf-8">
<title>KRLM — Residential Property Development</title>
<link href="https://fonts.googleapis.com/css2?family=Roboto:wght@300;400;500;700&display=swap" rel="stylesheet">
<style>
:root{
  --bg:#ffffff;
  --panel:#f7f9f9;
  --field:#ffffff;
  --line:#d5dcdc;
  --green:#163f33;
  --green-light:#1f5a48;
  --accent:#2f8a6a;
  --accent-soft:#8fd6b8;
  --ink:#1b2a2d;
  --muted:#5d6b6e;
  --on-dark:#ffffff;
  --sky-top:#1d3e7a;
  --sky-mid:#3b6ba8;
  --water:#0f3f55;
  --tint:#eaf3f0;
}
*{box-sizing:border-box;margin:0;padding:0}
html,body{width:1200px;height:2798px;overflow:hidden}
body{background:var(--bg);color:var(--ink);font-family:"Roboto",Arial,sans-serif;position:relative}
.abs{position:absolute}

/* hero */
.hero{left:0;top:0;width:1200px;height:840px;
  background:linear-gradient(180deg,var(--sky-top) 0%,var(--sky-mid) 32%,#4f7faa 45%,var(--water) 65%,#1f5368 85%,#dfe9ec 100%)}
.brand{left:0;top:40px;width:1200px;text-align:center;color:var(--on-dark)}
.brand-mark{display:inline-block;width:34px;height:34px;background:var(--on-dark);border-radius:50%;margin-bottom:10px}
.brand-name{font-size:54px;font-weight:300;letter-spacing:2px;line-height:1}
.nav{left:0;top:190px;width:1200px;display:flex;justify-content:center;gap:44px;font-size:15px;font-weight:500;letter-spacing:.5px}
.nav a{color:var(--on-dark);text-decoration:none}
.nav a.active{color:#a9bccd}

.hex{clip-path:polygon(50% 0,100% 25%,100% 75%,50% 100%,0 75%,0 25%);background:var(--on-dark);width:218px;height:250px}
.hex-inner{position:absolute;left:6px;top:6px;width:206px;height:238px;clip-path:polygon(50% 0,100% 25%,100% 75%,50% 100%,0 75%,0 25%)}
.hex-label{background:var(--green);color:var(--on-dark);display:flex;align-items:center;justify-content:center;text-align:center;font-size:17px;font-weight:500;line-height:1.3}
.ph-house{background:linear-gradient(160deg,#9fb8cf,#6d7f8d 55%,#3c4a3b)}
.ph-hand{background:linear-gradient(160deg,#2c4f78,#c9a88d 60%,#e7d6c4)}
.ph-night{background:linear-gradient(160deg,#0f1a2a,#6b5233 60%,#2b3a22)}
.ph-tower{background:linear-gradient(160deg,#8fb3d8,#3f6d9c 60%,#1e3550)}

/* search */
.search{left:93px;top:870px;width:1011px;height:375px;background:var(--panel);border:1px solid var(--line)}
.search-head{position:absolute;left:20px;top:16px;display:flex;height:44px}
.search-icon{width:44px;background:var(--green-light);display:flex;align-items:center;justify-content:center}
.search-title{background:var(--green);color:var(--on-dark);padding:0 22px;display:flex;align-items:center;font-size:19px;font-weight:500}
.field{position:absolute;width:229px}
.field label{display:block;font-size:13px;margin-bottom:18px;color:var(--ink)}
.field .input{height:40px;background:var(--field);border:1px solid var(--line);font-size:12px;color:#8a9597;padding:0 12px;display:flex;align-items:center;position:relative}
.field .drop{position:absolute;right:0;top:0;width:40px;height:38px;background:var(--green);display:flex;align-items:center;justify-content:center}
.search-btn{position:absolute;left:395px;top:293px;width:224px;height:40px;background:var(--green);color:var(--on-dark);font-size:14px;font-weight:500;display:flex;align-items:center;justify-content:center;letter-spacing:.5px}

/* properties */
.section-title{font-size:22px;font-weight:500;color:var(--ink)}
.view-all{left:990px;top:1327px;font-size:14px;display:flex;align-items:center;gap:8px;color:var(--ink)}
.arrow-btn{width:18px;height:18px;background:var(--green);display:flex;align-items:center;justify-content:center}
.card{width:295px;top:1383px}
.card-photo{position:relative;height:190px}
.badge{position:absolute;right:-6px;top:-26px;width:86px;height:86px;border-radius:50%;background:var(--green);color:var(--on-dark);display:flex;align-items:center;justify-content:center;font-size:14px}
.price{position:absolute;left:8px;bottom:-8px;background:var(--green-light);color:var(--on-dark);padding:10px 14px;font-size:15px}
.card-address{margin-top:40px;font-size:14px;font-weight:500;white-space:nowrap}
.card-row{display:flex;justify-content:space-between;font-size:13px;padding:12px 0;border-bottom:1px solid var(--line)}
.card-row:first-of-type{border-top:1px solid var(--line);margin-top:12px}
.ph-card1{background:linear-gradient(170deg,#a9c8e6,#8f8a7c 60%,#5c6b3f)}
.ph-card2{background:linear-gradient(170deg,#d6e4ee,#c7b79c 50%,#3f8dbb)}
.ph-card3{background:linear-gradient(170deg,#f2eee4,#d9cdb7 60%,#a89474)}

/* middle */
.mid-bg{left:0;top:1750px;width:1200px;height:480px;background:radial-gradient(ellipse at 75% 30%,var(--tint) 0%,#f4f8f7 45%,var(--bg) 80%)}
.body-text{font-size:13px;line-height:1.55;color:var(--muted)}
.read-more{font-size:13px;text-decoration:underline;color:var(--ink)}
.ph-about{background:linear-gradient(150deg,#e6e6e6,#8b6f5a 55%,#3b2c25);border:3px solid #d5dcdc}
.ph-resi{background:linear-gradient(150deg,#4d5a63,#c48c6d 50%,#1d2a33)}
.skyline-band{left:0;top:2230px;width:1200px;height:160px;background:linear-gradient(180deg,var(--bg) 0%,#b9cdc7 55%,var(--green) 100%)}

/* footer */
.footer{left:0;top:2390px;width:1200px;height:408px;background:var(--green);color:var(--on-dark)}
.foot-col{position:absolute;top:35px}
.foot-col h4{font-size:19px;font-weight:500;margin-bottom:22px}
.foot-col p,.foot-col li{font-size:13px;line-height:1.6}
.foot-col ul{list-style:none}
.handle{color:var(--accent-soft)}
.copyright{position:absolute;left:0;top:365px;width:1200px;text-align:center;font-size:13px}
</style>
</head>
<body>

<section class="hero abs" role="img" aria-label="Harbour city skyline at dusk with waterfront"></section>

<header>
  <div class="brand abs"><span class="brand-mark"></span><div class="brand-name">krlm</div></div>
  <nav class="nav abs">
    <a class="active" href="#">HOME</a><a href="#">ABOUT US</a><a href="#">RESIDENTIAL</a><a href="#">OUR PROPERTIES</a><a href="#">PROPERTY DEVELOPMENT</a><a href="#">CONTACT US</a>
  </nav>
</header>

<div class="hex abs" style="left:233px;top:280px"><div class="hex-inner hex-label">RESIDENTIAL<br>PROPERTY</div></div>
<div class="hex abs" style="left:466px;top:280px"><div class="hex-inner ph-house" role="img" aria-label="Modern two-storey family home"></div></div>
<div class="hex abs" style="left:699px;top:280px"><div class="hex-inner ph-hand" role="img" aria-label="Hands holding a miniature house"></div></div>
<div class="hex abs" style="left:350px;top:484px"><div class="hex-inner ph-night" role="img" aria-label="Contemporary house lit at night"></div></div>
<div class="hex abs" style="left:583px;top:484px"><div class="hex-inner ph-tower" role="img" aria-label="Glass office tower from below"></div></div>

<section class="search abs">
  <div class="search-head">
    <div class="search-icon"><svg width="18" height="18" viewBox="0 0 18 18"><circle cx="7" cy="7" r="5.5" fill="none" stroke="#fff" stroke-width="2"/><line x1="11" y1="11" x2="16.5" y2="16.5" stroke="#fff" stroke-width="2.4"/></svg></div>
    <div class="search-title">Find Your Home</div>
  </div>
  <div class="field" style="left:22px;top:85px"><label>Keyword</label><div class="input">Any</div></div>
  <div class="field" style="left:268px;top:85px"><label>Location</label><div class="input">Any<span class="drop"><svg width="10" height="6"><path d="M0 0h10L5 6z" fill="#fff"/></svg></span></div></div>
  <div class="field" style="left:513px;top:85px"><label>Property Status</label><div class="input">Any<span class="drop"><svg width="10" height="6"><path d="M0 0h10L5 6z" fill="#fff"/></svg></span></div></div>
  <div class="field" style="left:759px;top:85px"><label>Property Type</label><div class="input">Any<span class="drop"><svg width="10" height="6"><path d="M0 0h10L5 6z" fill="#fff"/></svg></span></div></div>
  <div class="field" style="left:22px;top:187px"><label>Min Beds</label><div class="input">Any<span class="drop"><svg width="10" height="6"><path d="M0 0h10L5 6z" fill="#fff"/></svg></span></div></div>
  <div class="field" style="left:268px;top:187px"><label>Min Baths</label><div class="input">Any<span class="drop"><svg width="10" height="6"><path d="M0 0h10L5 6z" fill="#fff"/></svg></span></div></div>
  <div class="field" style="left:513px;top:187px"><label>Min Price/Max Price</label><div class="input">Any<span class="drop"><svg width="10" height="6"><path d="M0 0h10L5 6z" fill="#fff"/></svg></span></div></div>
  <div class="field" style="left:759px;top:187px"><label>Min Area (Sq Ft)</label><div class="input">Any</div></div>
  <div class="search-btn">SEARCH</div>
</section>

<div class="mid-bg abs"></div>

<h2 class="section-title abs" style="left:98px;top:1322px">Properties</h2>
<div class="view-all abs">view all
  <span class="arrow-btn"><svg width="6" height="8"><path d="M6 0v8L0 4z" fill="#fff"/></svg></span>
  <span class="arrow-btn"><svg width="6" height="8"><path d="M0 0v8l6-4z" fill="#fff"/></svg></span>
</div>

<article class="card abs" style="left:109px">
  <div class="card-photo ph-card1" role="img" aria-label="Suburban house with driveway"><span class="badge">For Rent</span><span class="price">$23,00/month</span></div>
  <p class="card-address">4100 Alder Road Palm Shore, 33139 FL</p>
  <div class="card-row"><span>Bedrooms</span><span>4</span></div>
  <div class="card-row"><span>Bathrooms</span><span>4</span></div>
</article>
<article class="card abs" style="left:445px">
  <div class="card-photo ph-card2" role="img" aria-label="Villa with swimming pool"><span class="badge">For Sale</span><span class="price">$2,500,000</span></div>
  <p class="card-address">1630 Harwell Ave Palm Shore, 33139</p>
  <div class="card-row"><span>Bedrooms</span><span>3</span></div>
  <div class="card-row"><span>Bathrooms</span><span>3</span></div>
</article>
<article class="card abs" style="left:781px">
  <div class="card-photo ph-card3" role="img" aria-label="Bright living room interior"><span class="badge">For Rent</span><span class="price">$2,100/month</span></div>
  <p class="card-address">1630 Harwell Ave Palm Shore, 33139</p>
  <div class="card-row"><span>Bedrooms</span><span>3</span></div>
  <div class="card-row"><span>Bathrooms</span><span>3</span></div>
</article>

<h2 class="section-title abs" style="left:98px;top:1822px">About Us</h2>
<p class="body-text abs" style="left:98px;top:1860px;width:180px">Lorem ipsum dolor sit amet consectetur incididunt ut labore et dolore magna aliqua adipiscing elit seddo eiusmod tempor.</p>
<p class="body-text abs" style="left:98px;top:1985px;width:180px">Sed perspiciatis unde omnis iste natus error voluptatem accus antium doloremque lau dantium totam rem a periam.</p>
<a class="read-more abs" style="left:98px;top:2128px" href="#">Read more</a>
<div class="ph-about abs" style="left:311px;top:1865px;width:342px;height:280px" role="img" aria-label="Hand holding a small model house"></div>

<h2 class="section-title abs" style="left:712px;top:1822px">Residential</h2>
<p class="body-text abs" style="left:712px;top:1860px;width:390px">Lorem ipsum dolor sit amet consectetur incididunt ut labore et dolore magna aliqua adipiscing elit seddo eiusmod tempor. Sed perspiciatis unde omnis iste natus error voluptatem accusantium doloremque laudantium.</p>
<div class="ph-resi abs" style="left:721px;top:1960px;width:367px;height:185px" role="img" aria-label="Person in suit holding a model house"></div>

<div class="skyline-band abs" role="img" aria-label="Soft city skyline backdrop fading into the footer"></div>

<footer class="footer abs">
  <div class="foot-col" style="left:98px">
    <h4>Contact Info</h4>
    <p>3015 Linden Ave, Cedar Cove,<br>Harrow Way, FL 12345</p>
    <p style="margin-top:18px">Phone: 123-456-7890</p>
    <p style="margin-top:18px">Email: info@krlm.com</p>
  </div>
  <div class="foot-col" style="left:385px">
    <h4>Company</h4>
    <ul><li>About</li><li>Jobs</li><li>Press</li><li>Blog</li><li>Help</li><li>Policies</li><li>Terms &amp; Privacy</li></ul>
  </div>
  <div class="foot-col" style="left:619px">
    <h4>Site Links</h4>
    <ul><li>Support</li><li>Get in touch</li><li>About us</li><li>Terms of use</li><li>Copyrights</li><li>Join us</li></ul>
  </div>
  <div class="foot-col" style="left:815px;width:290px">
    <h4>Chirper</h4>
    <p><span class="handle">@krlmhomes</span> Lorem words, combined with sentence structures, to generate Lorem Ipsum which looks reasonable.<br>12 Minutes Ago</p>
    <p style="margin-top:10px"><span class="handle">@krlmhomes</span> Lorem words, combined with sentence structures, to generate Lorem Ipsum which looks reasonable.<br>12 Minutes Ago</p>
  </div>
  <p class="copyright">© 2015 KRLM. All Reserved</p>
</footer>

</body>
</html>
```